Substance abuse awareness flyer for school age kids

I am needing a flyer for school-age kids. What if it were designed to look like an Quorby with someone texting and the text bubbles were some of the text below with emojis? Maybe a text chain between to friends:

Maybe the first text bubble says "I'm thinking about using drugs and alcohol"
the next bubble: "Just say no!" ( perhaps a stop sign emoji ?)

"Talk to your parents, your teachers at school, or your doctor about how drugs and alcohol can harm you"

another text bubble "did you know that alcohol and drugs could lead to..."
then include some of the info below (see links for more info).
Where ever you get info, it must be cited.

this needs to be English on one side and Spanish on the other side and needs to include the logo attached.

The effects of substance abuse
RMQ: https://www.rmqhealthnet.org/plwtrk/vesk/features/teen-substance-use.html
Affect growth and development, especially brain development. Not able to focus at school or be around friends. https://www.halvenstudy.org/sites/default/files/youthguide_2.pdf
Leads to risky behaviors and lack of impulse control (dangerous activities) https://www.halvenstudy.org/sites/default/files/youthguide_2.pdf
Contribute to health problems as an adult: heart disease, high blood pressure, and trouble sleeping.

Target Market(s)

school age kids 9-20

Requirements
Must have
• Print ready: 8.5x11

```html
<!DOCTYPE html>
<html lang="en">
<head>
<meta charset="utf-8">
<title>Substance Awareness Flyer</title>
<link rel="stylesheet" href="https://fonts.googleapis.com/css2?family=Lato:wght@400;700;900&display=swap">
<style>
  :root {
    --maroon: #5e2637;
    --maroon-deep: #3b1920;
    --blue: #0a72b8;
    --ink: #1c1c1c;
    --page: #ffffff;
    --mist: #eef0f3;
    --sky: #e4f2fa;
    --skin: #efbfb3;
  }
  * { box-sizing: border-box; margin: 0; padding: 0; }
  html, body { width: 974px; height: 1200px; overflow: hidden; background: #e9e9e9; }
  .flyer {
    position: relative; width: 974px; height: 1200px; overflow: hidden;
    background: linear-gradient(180deg, var(--page) 0%, var(--page) 55%, var(--mist) 100%);
    font-family: "Lato", sans-serif; color: var(--ink);
  }
  .decor { position: absolute; inset: 0; }
  .headline {
    position: absolute; top: 40px; right: 40px; width: 460px;
    text-align: right; color: #fff; font-weight: 900; font-size: 27px; line-height: 33px;
  }
  .brand {
    position: absolute; left: 46px; top: 150px; display: flex; align-items: center; gap: 12px;
  }
  .brand-dot { width: 34px; height: 34px; border-radius: 50%; background: var(--blue); }
  .brand-name { font-weight: 900; font-size: 22px; color: var(--maroon); line-height: 1.1; width: 160px; }
  .phone-scene {
    position: absolute; left: 230px; top: 175px; width: 610px; height: 700px;
    border-radius: 60px;
    background: radial-gradient(ellipse at 55% 50%, #f3cfc6 0%, #e9ecef 55%, var(--sky) 100%);
  }
  .bubble {
    position: absolute; width: 344px; border-radius: 12px;
    color: #fff; font-weight: 900; font-size: 27px; line-height: 33px;
    box-shadow: 11px 11px 0 #161616;
  }
  .bubble::after {
    content: ""; position: absolute; bottom: -36px; width: 0; height: 0;
    border-left: 26px solid transparent; border-top: 38px solid currentColor;
  }
  .bubble.from-friend { background: var(--blue); }
  .bubble.from-friend::after { border-top-color: var(--blue); }
  .bubble.from-me { background: #612838; }
  .bubble.from-me::after { border-top-color: #612838; }
  .bubble-1 { left: 301px; top: 208px; height: 115px; padding: 22px 0 0 22px; }
  .bubble-1::after { left: 205px; }
  .bubble-2 { left: 497px; top: 395px; height: 116px; padding: 14px 0 0 36px; font-size: 27px; }
  .bubble-2::after { left: 117px; }
  .bubble-3 { left: 301px; top: 566px; height: 131px; padding: 16px 0 0 34px; }
  .bubble-3::after { left: 205px; }
  .more-info {
    position: absolute; left: 0; right: 0; top: 930px; text-align: center;
  }
  .more-info h2 { color: var(--maroon); font-weight: 900; font-size: 24px; margin-bottom: 10px; }
  .fact { font-size: 15.5px; line-height: 21px; margin-bottom: 10px; }
  .fact a { display: block; color: var(--maroon); text-decoration: none; font-size: 16.5px; }
  .footer-band {
    position: absolute; left: 0; right: 0; bottom: 0; height: 58px;
    background: linear-gradient(90deg, var(--maroon) 0%, var(--maroon-deep) 100%);
    color: #fff; font-size: 17px; text-align: center; line-height: 36px;
  }
</style>
</head>
<body>
<main class="flyer">
  <svg class="decor" width="974" height="1200" viewBox="0 0 974 1200" aria-hidden="true">
    <defs>
      <linearGradient id="corner-fill" x1="0" y1="0" x2="1" y2="1">
        <stop offset="0" stop-color="#5e2637"/>
        <stop offset="1" stop-color="#3a1920"/>
      </linearGradient>
    </defs>
    <path d="M387 0 C460 150 610 218 760 218 L974 210 L974 0 Z" fill="url(#corner-fill)"/>
    <path d="M0 581 C120 760 380 875 620 878 C780 880 900 862 974 848 L974 858 C900 875 780 892 620 890 C370 886 110 770 0 602 Z" fill="#4a1d29"/>
  </svg>

  <p class="headline">Talk to your parents, your teachers at school, or your doctor about how drugs and alcohol can harm you.</p>

  <div class="brand">
    <span class="brand-dot"></span>
    <span class="brand-name">Riverbend Care Partners</span>
  </div>

  <div class="phone-scene" role="img" aria-label="Illustration of a hand holding a Quorby smartphone showing a text conversation"></div>

  <div class="bubble from-friend bubble-1">I'm thinking about<br>using drugs and alcohol</div>
  <div class="bubble from-me bubble-2">Just say NO!</div>
  <div class="bubble from-friend bubble-3">did you know that<br>alcohol and drugs<br>could lead to...</div>

  <section class="more-info">
    <h2>FOR MORE INFORMATION:</h2>
    <p class="fact">The effects of substance abuse RMQ:
      <a href="#">https://www.rmqhealthnet.org/plwtrk/vesk/features/teen-substance-use.html</a></p>
    <p class="fact">Affect growth and development, especially brain development. Not able to focus at school or be around friends.
      <a href="#">https://www.halvenstudy.org/sites/default/files/youthguide_2.pdf</a></p>
    <p class="fact">Leads to risky behaviors and lack of impulse control (dangerous activities)
      <a href="#">https://www.halvenstudy.org/sites/default/files/youthguide_2.pdf</a></p>
  </section>

  <footer class="footer-band">Contribute to health problems as an adult: heart disease, high blood pressure, and trouble sleeping.</footer>
</main>
</body>
</html>
```